Travel Agency Website - Simple General

Need a 7 page simple design that is pretty repetitive. Need to be able to load quickly that is SEO optimized. Trying to give ideas on what they can do, be personal as we are local, but at the same time come across as professional and get information easily with little burden.

- Landing Page
- Brimwell Vacations Page
- Family Trips
- Road Trips from Texas
- Other Destinations
- About Us Page
- Contact Us Page

Target Market(s)

Families

Coding

Coded - Design and coding required

Number of Pages Required

5+ page

Colors

Designer to choose colors to be used in the design.

Requirements
Must have
• Like it to flow easily with our logo. Use that for colors, etc.

```html
<!DOCTYPE html>
<html lang="en">
<head>
<meta charset="utf-8">
<title>Hum As You Roam — Family Travel Experts</title>
<meta name="viewport" content="width=1200">
<link href="https://fonts.googleapis.com/css2?family=Montserrat:ital,wght@0,600;0,700;0,800;1,400&family=Inter:ital,wght@0,400;0,500;0,600;1,400&display=swap" rel="stylesheet">
<style>
:root{
  --navy:#0b1121;
  --navy-2:#121a2c;
  --card:#161e30;
  --footer:#1d2c4e;
  --gold:#d9a55a;
  --gold-soft:#e3b46c;
  --coral:#e8694a;
  --white:#ffffff;
  --muted:#aab2c2;
  --line:rgba(255,255,255,.12);
}
*{box-sizing:border-box;margin:0;padding:0}
html,body{width:1200px;height:3606px;overflow:hidden}
body{background:var(--navy);color:var(--white);font-family:"Inter",sans-serif;position:relative}
.heading{font-family:"Montserrat",sans-serif}
.eyebrow{font-family:"Montserrat",sans-serif;font-size:10px;font-weight:700;letter-spacing:5px;color:var(--gold);text-transform:uppercase;display:flex;align-items:center;justify-content:center;gap:6px}
.section-title{font-family:"Montserrat",sans-serif;font-weight:700;font-size:46px;text-align:center;margin-top:18px}

/* nav */
.site-nav{position:absolute;top:0;left:0;width:1200px;height:78px;z-index:5;display:flex;align-items:center}
.brand{position:absolute;left:118px;top:11px;width:60px;height:55px;background:var(--white);border-radius:3px;display:flex;align-items:center;justify-content:center;text-align:center;font-family:"Montserrat",sans-serif;font-weight:600;font-size:9px;line-height:1.15;color:#2d5f6b;padding:4px}
.nav-links{position:absolute;left:259px;top:32px;display:flex;gap:32px;font-size:11px;font-weight:600}
.nav-links a{color:var(--white);text-decoration:none}
.nav-links a.active{color:var(--gold)}
.btn{display:inline-flex;align-items:center;justify-content:center;gap:8px;font-family:"Montserrat",sans-serif;font-weight:700;letter-spacing:1.5px;text-transform:uppercase;text-decoration:none;border-radius:6px}
.btn-gold{background:var(--gold);color:#2a1d0b}
.btn-ghost{background:rgba(255,255,255,.1);border:1px solid rgba(255,255,255,.35);color:var(--white)}
.nav-cta{position:absolute;left:927px;top:25px;width:154px;height:28px;font-size:10px}

/* hero */
.hero{position:relative;height:581px;overflow:hidden}
.hero-photo{position:absolute;inset:0;background:
 linear-gradient(180deg,rgba(11,17,33,.25) 0%,rgba(11,17,33,.1) 45%,rgba(11,17,33,.75) 80%,var(--navy) 100%),
 linear-gradient(180deg,#3d5e86 0%,#6b8fb0 30%,#3f6f7a 45%,#1f4c6a 55%,#a9a498 62%,#6f6a66 75%,#2a2f3e 100%)}
.hero-content{position:absolute;left:0;width:1200px;top:136px;text-align:center}
.hero-title{font-family:"Montserrat",sans-serif;font-weight:800;font-size:92px;line-height:100px;margin-top:14px;letter-spacing:-1px}
.hero-title .gold{color:var(--gold);display:block}
.hero-quote{font-style:italic;font-size:18px;color:#e8ebf1;margin-top:18px}
.hero-actions{display:flex;justify-content:center;gap:12px;margin-top:28px}
.hero-actions .btn{height:48px;font-size:14px}
.hero-actions .btn-gold{width:218px}
.hero-actions .btn-ghost{width:203px}
.discover{position:absolute;top:517px;width:1200px;text-align:center;font-size:8px;letter-spacing:4px;color:rgba(217,165,90,.6);font-family:"Montserrat",sans-serif}
.discover svg{display:block;margin:6px auto 0}

/* specialties */
.specialties{height:889px;padding-top:75px}
.trip-grid{position:relative;margin-top:0}
.trip-card{position:absolute;border-radius:18px;overflow:hidden}
.trip-photo{position:absolute;inset:0}
.trip-card::after{content:"";position:absolute;inset:0;background:linear-gradient(180deg,rgba(11,17,33,0) 40%,rgba(11,17,33,.55) 100%)}
.trip-text{position:absolute;left:31px;bottom:57px;z-index:2}
.trip-text h3{font-family:"Montserrat",sans-serif;font-weight:700;font-size:24px}
.trip-text p{font-size:10.5px;color:var(--gold);margin-top:4px}
.trip-text .explore{font-family:"Montserrat",sans-serif;font-size:9px;letter-spacing:1.5px;font-weight:700;color:#d4d8e0;margin-top:14px;display:flex;gap:5px;align-items:center}
.card-brim{left:125px;top:108px;width:630px;height:292px}
.card-family{left:767px;top:108px;width:308px;height:292px}
.card-texas{left:125px;top:418px;width:308px;height:296px}
.card-other{left:446px;top:418px;width:629px;height:296px}
.card-other .trip-text{bottom:40px}

/* why */
.why{position:relative;height:589px;overflow:hidden;padding-top:101px}
.why-photo{position:absolute;inset:0;background:
 linear-gradient(180deg,rgba(20,28,40,.8),rgba(20,28,40,.55) 60%,rgba(40,30,25,.7)),
 linear-gradient(180deg,#4b5560 0%,#3a4a48 40%,#2b3a33 65%,#5a3f2c 85%,#3a2a20 100%)}
.why > *:not(.why-photo){position:relative}
.gold-rule{width:64px;height:3px;background:var(--gold);margin:18px auto 0;border-radius:2px}
.why-grid{display:flex;gap:19px;padding-left:125px;margin-top:90px}
.why-card{width:224px;height:223px;border-radius:18px;background:rgba(110,105,100,.35);border:1px solid rgba(255,255,255,.12);text-align:center;padding:26px 20px 0}
.why-icon{width:50px;height:50px;border-radius:10px;background:rgba(217,165,90,.28);margin:0 auto;display:flex;align-items:center;justify-content:center}
.why-card h3{font-family:"Montserrat",sans-serif;font-weight:700;font-size:16px;line-height:20px;margin-top:20px}
.why-card p{font-size:10.5px;line-height:18px;color:#d6d8dd;margin-top:12px}

/* testimonials */
.stories{height:579px;padding-top:102px}
.story-grid{display:flex;gap:25px;padding-left:125px;margin-top:64px}
.story{width:300px;height:227px;border-radius:18px;background:var(--navy-2);border:1px solid var(--line);padding:25px 25px 0}
.stars{display:flex;gap:2px}
.story blockquote{font-style:italic;font-size:13.5px;line-height:23px;color:#c6ccd8;margin-top:14px;height:84px}
.story .who{border-top:1px solid var(--line);margin-top:22px;padding-top:20px}
.story .who strong{font-size:12.5px;font-weight:600;display:block}
.story .who span{font-size:10.5px;color:var(--gold)}

/* cta */
.cta{position:relative;height:703px;overflow:hidden}
.cta-photo{position:absolute;inset:0;background:
 linear-gradient(180deg,rgba(11,17,33,.55),rgba(11,17,33,.35) 50%,rgba(11,17,33,.6)),
 linear-gradient(100deg,#3b3a3c 0%,#5e5448 35%,#7b6a56 55%,#4d4038 75%,#2a2628 100%)}
.cta-card{position:absolute;left:300px;top:125px;width:600px;height:464px;border-radius:36px;background:rgba(120,110,100,.42);border:1px solid rgba(255,255,255,.18);text-align:center;padding-top:65px}
.cta-card h2{font-family:"Montserrat",sans-serif;font-weight:700;font-size:46px;line-height:58px;margin-top:16px}
.cta-card h2 .coral{color:var(--coral);display:block}
.cta-card .gold-rule{margin-top:22px}
.cta-card p{font-style:italic;font-size:14px;line-height:22px;color:#dcdde2;width:440px;margin:30px auto 0}
.cta-card .btn{width:242px;height:52px;font-size:15px;margin-top:32px}

/* footer */
.site-footer{height:266px;background:var(--footer);position:relative;font-size:11px}
.foot-col{position:absolute;top:52px}
.foot-brand{left:125px;top:50px;width:245px}
.foot-logo{width:62px;height:57px;background:var(--white);border-radius:2px;display:flex;align-items:center;justify-content:center;text-align:center;font-family:"Montserrat",sans-serif;font-weight:600;font-size:9px;line-height:1.15;color:#2d5f6b;padding:4px}
.foot-brand p{font-size:11px;line-height:18px;margin-top:20px;color:#e3e6ee}
.foot-col h4{font-family:"Montserrat",sans-serif;font-weight:700;font-size:13.5px}
.foot-col ul{list-style:none;margin-top:14px}
.foot-col li{margin-bottom:17px;font-size:11px;color:#d8dce6}
.col-links{left:372px}
.col-explore{left:619px}
.col-contact{left:866px}
.col-contact li{display:flex;gap:10px;align-items:center;margin-bottom:13px}
.socials{display:flex;gap:18px;margin-left:4px;margin-top:14px}
.socials span{width:20px;height:20px;border-radius:50%;border:2px solid var(--white);display:block}
.copyright{position:absolute;bottom:6px;width:1200px;text-align:center;font-size:9px;color:#9aa4ba}
</style>
</head>
<body>

<header class="site-nav">
  <div class="brand">Hum As You Roam</div>
  <nav class="nav-links">
    <a class="active" href="#">Home</a>
    <a href="#">Brimwell Vacations</a>
    <a href="#">Family Trips</a>
    <a href="#">Texas Road Trips</a>
    <a href="#">Other Destinations</a>
    <a href="#">About Us</a>
  </nav>
  <a class="btn btn-gold nav-cta" href="#">Start Planning</a>
</header>

<section class="hero">
  <div class="hero-photo" role="img" aria-label="Tropical beach with palm tree, straw umbrella, lounge chairs and mountains across a blue bay"></div>
  <div class="hero-content">
    <div class="eyebrow">
      <svg width="12" height="12" viewBox="0 0 24 24" fill="none" stroke="#d9a55a" stroke-width="2"><path d="M12 3l2 6 6 2-6 2-2 6-2-6-6-2 6-2z"/></svg>
      Your Family Travel Experts
    </div>
    <h1 class="hero-title"><span class="gold">Hum As You</span>Roam Free</h1>
    <p class="hero-quote">"Travel is the only thing you buy that makes you richer."</p>
    <div class="hero-actions">
      <a class="btn btn-gold" href="#">Start Planning</a>
      <a class="btn btn-ghost" href="#">Explore Trips</a>
    </div>
  </div>
  <div class="discover">DISCOVER ADVENTURES
    <svg width="14" height="10" viewBox="0 0 14 10" fill="none" stroke="#d9a55a" stroke-width="1.6"><path d="M2 2l5 5 5-5"/></svg>
  </div>
</section>

<section class="specialties">
  <div class="eyebrow">
    <svg width="12" height="12" viewBox="0 0 24 24" fill="none" stroke="#d9a55a" stroke-width="2"><path d="M3 6l6-2 6 2 6-2v14l-6 2-6-2-6 2z"/><path d="M9 4v14M15 6v14"/></svg>
    Our Specialties
  </div>
  <h2 class="section-title">Your Next Adventure</h2>
  <div class="trip-grid">
    <a class="trip-card card-brim" href="#">
      <div class="trip-photo" role="img" aria-label="City bridge and skyline lit up at night over a river" style="background:linear-gradient(180deg,#1f2a3c 0%,#3b4a5e 40%,#6a5238 65%,#2a2a30 100%)"></div>
      <div class="trip-text"><h3>Brimwell Vacations</h3><p>Land and Sea — Where Magic Lives</p></div>
    </a>
    <a class="trip-card card-family" href="#">
      <div class="trip-photo" role="img" aria-label="Family silhouettes watching a sunset over the sea" style="background:linear-gradient(180deg,#4d6a8c 0%,#c98a55 45%,#e09a55 60%,#3a3a44 85%,#1e2232 100%)"></div>
      <div class="trip-text"><h3>Family Trips</h3><p>Memories for a Lifetime</p></div>
    </a>
    <a class="trip-card card-texas" href="#">
      <div class="trip-photo" role="img" aria-label="Red suspension bridge under a teal sky" style="background:linear-gradient(160deg,#1f6a74 0%,#3a8a8a 35%,#8a4a3a 60%,#3a4050 100%)"></div>
      <div class="trip-text"><h3>Texas Road Trips</h3><p>With Piney Van Rentals</p></div>
    </a>
    <a class="trip-card card-other" href="#">
      <div class="trip-photo" role="img" aria-label="Travel map with notebook, pencil and camera lens on a table" style="background:linear-gradient(120deg,#7a6a58 0%,#b9bcbd 30%,#d4d5d2 55%,#8e9296 80%,#5a5e68 100%)"></div>
      <div class="trip-text"><h3>Other Destinations</h3><p>Explore the World</p>
        <div class="explore">EXPLORE <svg width="10" height="8" viewBox="0 0 10 8" fill="none" stroke="#d4d8e0" stroke-width="1.4"><path d="M1 4h7M5 1l3 3-3 3"/></svg></div>
      </div>
    </a>
  </div>
</section>

<section class="why">
  <div class="why-photo" role="img" aria-label="Wooden boat bow on a mountain lake surrounded by forested cliffs"></div>
  <div class="eyebrow">
    <svg width="13" height="13" viewBox="0 0 24 24" fill="none" stroke="#d9a55a" stroke-width="2"><path d="M12 3l2.8 5.7 6.2.9-4.5 4.4 1 6.2L12 17.3 6.5 20.2l1-6.2L3 9.6l6.2-.9z"/></svg>
    Why Choose Us
  </div>
  <h2 class="section-title">Your Travel Partners</h2>
  <div class="gold-rule"></div>
  <div class="why-grid">
    <div class="why-card">
      <div class="why-icon"><svg width="22" height="22" viewBox="0 0 24 24" fill="none" stroke="#f0c68a" stroke-width="1.8"><path d="M10 4l1.5 4.5L16 10l-4.5 1.5L10 16l-1.5-4.5L4 10l4.5-1.5z"/><path d="M18 14l.8 2.2L21 17l-2.2.8L18 20l-.8-2.2L15 17l2.2-.8z"/></svg></div>
      <h3>Personalized<br>Planning</h3>
      <p>Tailored itineraries that match your family's unique style and budget.</p>
    </div>
    <div class="why-card">
      <div class="why-icon"><svg width="22" height="22" viewBox="0 0 24 24" fill="none" stroke="#f0c68a" stroke-width="1.8"><circle cx="9" cy="8" r="3.5"/><path d="M2.5 20c0-3.6 2.9-6 6.5-6s6.5 2.4 6.5 6"/><path d="M15.5 4.6a3.5 3.5 0 010 6.8M18 14.5c2 .8 3.5 2.8 3.5 5.5"/></svg></div>
      <h3>Family Focused</h3>
      <p>As a local family ourselves, we know exactly what makes a trip special for all ages.</p>
    </div>
    <div class="why-card">
      <div class="why-icon"><svg width="22" height="22" viewBox="0 0 24 24" fill="none" stroke="#f0c68a" stroke-width="1.8"><path d="M3 6l6-2 6 2 6-2v14l-6 2-6-2-6 2z"/><path d="M9 4v14M15 6v14"/></svg></div>
      <h3>Local Support</h3>
      <p>Based in Texas, we're your neighbors and your personal travel concierge.</p>
    </div>
    <div class="why-card">
      <div class="why-icon"><svg width="22" height="22" viewBox="0 0 24 24" fill="none" stroke="#f0c68a" stroke-width="1.8"><circle cx="12" cy="12" r="9"/><path d="M12 7v5l3 2"/></svg></div>
      <h3>Stress-Free Travel</h3>
      <p>We handle the logistics so you can focus on making memories.</p>
    </div>
  </div>
</section>

<section class="stories">
  <div class="eyebrow">
    <svg width="13" height="13" viewBox="0 0 24 24" fill="none" stroke="#d9a55a" stroke-width="2"><path d="M4 17c2 0 4-2 4-5V6H3v6h5M15 17c2 0 4-2 4-5V6h-5v6h5"/></svg>
    What Families Say
  </div>
  <h2 class="section-title">Stories of Joy</h2>
  <div class="story-grid">
    <article class="story">
      <div class="stars">
        <svg width="64" height="11" viewBox="0 0 64 11" fill="#d9a55a"><g id="st"><path d="M5.5 0l1.6 3.5 3.9.4-2.9 2.6.8 3.8-3.4-2-3.4 2 .8-3.8L0 3.9l3.9-.4z"/></g><use href="#st" x="13"/><use href="#st" x="26"/><use href="#st" x="39"/><use href="#st" x="52"/></svg>
      </div>
      <blockquote>"They thought of everything we didn't. Our kids still talk about it every single day."</blockquote>
      <div class="who"><strong>Laura &amp; Ben T.</strong><span>Brimwell World Family Trip</span></div>
    </article>
    <article class="story">
      <div class="stars"><svg width="64" height="11" viewBox="0 0 64 11" fill="#d9a55a"><use href="#st"/><use href="#st" x="13"/><use href="#st" x="26"/><use href="#st" x="39"/><use href="#st" x="52"/></svg></div>
      <blockquote>"The van was perfect, the route was breathtaking. We found places we never would have discovered alone."</blockquote>
      <div class="who"><strong>The Alvarez Family</strong><span>Texas Road Trip Adventure</span></div>
    </article>
    <article class="story">
      <div class="stars"><svg width="64" height="11" viewBox="0 0 64 11" fill="#d9a55a"><use href="#st"/><use href="#st" x="13"/><use href="#st" x="26"/><use href="#st" x="39"/><use href="#st" x="52"/></svg></div>
      <blockquote>"From booking to boarding, we were completely taken care of. This was our best vacation ever."</blockquote>
      <div class="who"><strong>Claire &amp; Owen P.</strong><span>Brimwell Cruise — 7 Nights</span></div>
    </article>
  </div>
</section>

<section class="cta">
  <div class="cta-photo" role="img" aria-label="Traveller relaxing in an airport lounge with a suitcase as a plane takes off outside the window"></div>
  <div class="cta-card">
    <div class="eyebrow">
      <svg width="12" height="12" viewBox="0 0 24 24" fill="none" stroke="#d9a55a" stroke-width="2"><path d="M12 3l2 6 6 2-6 2-2 6-2-6-6-2 6-2z"/></svg>
      Let's Begin
    </div>
    <h2>Ready to Start<span class="coral">Your Journey?</span></h2>
    <div class="gold-rule"></div>
    <p>Contact us today for a free consultation. Let's make your dream vacation a reality with the personal touch your family deserves.</p>
    <a class="btn btn-gold" href="#">Get in Touch
      <svg width="12" height="10" viewBox="0 0 12 10" fill="none" stroke="#2a1d0b" stroke-width="1.6"><path d="M1 5h9M6 1l4 4-4 4"/></svg>
    </a>
  </div>
</section>

<footer class="site-footer">
  <div class="foot-col foot-brand">
    <div class="foot-logo">Hum As You Roam</div>
    <p>Making family memories easier with personalized, stress-free travel planning. Your local experts for magical vacations.</p>
  </div>
  <div class="foot-col col-links">
    <h4>Quick Links</h4>
    <ul><li>Home</li><li>Brimwell Vacations</li><li>Family Trips</li><li>Texas Road Trips</li></ul>
  </div>
  <div class="foot-col col-explore">
    <h4>Explore</h4>
    <ul><li>Other Destinations</li><li>About Us</li><li>Contact Us</li></ul>
  </div>
  <div class="foot-col col-contact">
    <h4>Get in Touch</h4>
    <ul>
      <li><svg width="14" height="14" viewBox="0 0 24 24" fill="none" stroke="#d9a55a" stroke-width="2"><path d="M5 3h4l2 5-2.5 1.5a11 11 0 006 6L16 13l5 2v4a2 2 0 01-2 2A17 17 0 013 5a2 2 0 012-2z"/></svg>111.111.1111</li>
      <li><svg width="14" height="14" viewBox="0 0 24 24" fill="none" stroke="#d9a55a" stroke-width="2"><rect x="3" y="5" width="18" height="14" rx="2"/><path d="M3 7l9 6 9-6"/></svg>hello@humasyouroam.com</li>
    </ul>
    <div class="socials"><span aria-label="Social profile"></span><span aria-label="Social profile"></span></div>
  </div>
  <div class="copyright">© 2026 Hum As You Roam Travel Co. All rights reserved.</div>
</footer>

</body>
</html>
```